Kestrel Facilities Business Card Design

We would now like to design business cards with the new Kestrel Facilities logo

Target Market(s)

Professional

Industry/Entity Type

Professional services

Contact Information for Business Card

Employee name, title, phone number, email address, corporate office address and logo.

Font styles to use
Sans Serif

Colors
0054AA
0677BA
7BADD7
CADEEF
E8F1F8

Requirements
Must have
• My logo
Should not have
• any other pictures or images besides my logo

```html
<!DOCTYPE html>
<html lang="en">
<head>
<meta charset="UTF-8">
<title>Kestrel Facilities Business Card</title>
<link href="https://fonts.googleapis.com/css2?family=Rubik:wght@400;500;700&display=swap" rel="stylesheet">
<style>
  :root {
    --brand-blue: #0054AA;
    --panel-blue: #0648b8;
    --panel-blue-light: #1a66d6;
    --frame-blue: #1f55b8;
    --ice: #E8F1F8;
    --mist: #CADEEF;
    --sand: #e9dcc6;
    --text-light: #dfe8f5;
    --page: #d9dde2;
  }
  * { box-sizing: border-box; margin: 0; padding: 0; }
  html, body { width: 1200px; height: 969px; overflow: hidden; }
  body {
    background: var(--page);
    font-family: "Rubik", sans-serif;
    position: relative;
  }
  .business-card {
    position: absolute;
    left: 100px; top: 200px;
    width: 1000px; height: 570px;
    background: linear-gradient(135deg, #f4f7fa, var(--ice) 60%, #eef2f6);
    border: 1px solid #b9c2cc;
  }
  .front-frame {
    position: absolute;
    left: 9px; top: 9px; right: 9px; bottom: 9px;
    border: 4px solid var(--frame-blue);
  }
  .contact-panel {
    position: absolute;
    left: 450px; top: 0; right: 0; bottom: 0;
    background: linear-gradient(160deg, var(--panel-blue), var(--panel-blue-light) 55%, var(--panel-blue));
    clip-path: polygon(0 0, 100% 0, 100% 100%, 0 100%, 0 241px, 35px 241px, 35px 152px, 0 152px);
  }
  .panel-frame {
    position: absolute;
    left: 0; top: 11px; right: 11px; bottom: 11px;
    border: 3px solid var(--sand);
    border-left: none;
    opacity: .85;
  }
  .brand {
    position: absolute;
    left: 70px; top: 215px;
    display: flex; align-items: center; gap: 18px;
    color: var(--brand-blue);
  }
  .brand-mark {
    width: 42px; height: 42px;
    background: var(--brand-blue);
  }
  .brand-name {
    font-weight: 700;
    font-size: 44px;
    line-height: 1.05;
    letter-spacing: 1px;
    text-transform: uppercase;
  }
  .contact-block {
    position: absolute;
    left: 570px; top: 160px;
    color: var(--text-light);
  }
  .person-name {
    font-weight: 500;
    font-size: 33px;
    letter-spacing: 1px;
    color: var(--sand);
    text-transform: uppercase;
  }
  .person-title { font-size: 23px; margin-top: 2px; }
  .address { font-size: 23px; line-height: 31px; margin-top: 22px; }
  .contact-list { list-style: none; margin-top: 22px; font-size: 23px; }
  .contact-list li { display: flex; align-items: center; height: 31px; }
  .contact-list svg { width: 20px; height: 20px; margin-right: 16px; fill: var(--text-light); }
</style>
</head>
<body>
  <div class="business-card">
    <div class="front-frame"></div>
    <div class="brand">
      <div class="brand-mark"></div>
      <div class="brand-name">Kestrel<br>Facilities</div>
    </div>
    <div class="contact-panel">
      <div class="panel-frame"></div>
    </div>
    <div class="contact-block">
      <p class="person-name">Daniel Hart</p>
      <p class="person-title">President</p>
      <p class="address">2140 Alder Ridge Road<br>Fairview, Alaska 99512</p>
      <ul class="contact-list">
        <li>
          <svg viewBox="0 0 24 24" aria-hidden="true"><path d="M6.6 10.8a15.1 15.1 0 0 0 6.6 6.6l2.2-2.2a1 1 0 0 1 1-.25 11.4 11.4 0 0 0 3.6.57 1 1 0 0 1 1 1V20a1 1 0 0 1-1 1A17 17 0 0 1 3 4a1 1 0 0 1 1-1h3.5a1 1 0 0 1 1 1c0 1.25.2 2.45.57 3.57a1 1 0 0 1-.25 1z"/></svg>
          555-018-2746
        </li>
        <li>
          <svg viewBox="0 0 24 24" aria-hidden="true"><path d="M3 5h18v14H3z M3 5l9 7 9-7" fill="none" stroke="#dfe8f5" stroke-width="2"/></svg>
          info@kestrelfacilities.com
        </li>
        <li>
          <svg viewBox="0 0 24 24" aria-hidden="true"><circle cx="12" cy="12" r="9" fill="none" stroke="#dfe8f5" stroke-width="2"/><path d="M3 12h18M12 3c3 3 3 15 0 18M12 3c-3 3-3 15 0 18" fill="none" stroke="#dfe8f5" stroke-width="1.6"/></svg>
          kestrelfacilities.com
        </li>
      </ul>
    </div>
  </div>
</body>
</html>
```